Business Card for Fashion House

We need a business card design for our personalize fashion service for our customers. the business card should reflect reliability, luxury and creativity.
The brand Gravetto is extracted from "Graceful Velvetto"; Gravetto provides fashion designs sprinkled with luxury and style tailored for our elite clients character profile.
Gravetto is created for those who embody class and elegance with a passion for style.
Target Market(s)
Affluent Customers
Industry/Entity Type
Fashion
Contact Information for Business Card
Samira Haddadin
Fashion Designer
Telephone: +971 4 555 0192
Mobile +971 50 555 0147
Emal info@gravetto-example.com
Website www.gravetto-example.com
Social Media Youtube g+ Facebook Instagram Pin /gravetto
Font styles to use
Other font styles liked:
- Audrey provided
Look and feel
Each slider illustrates characteristics of the customer's brand and the style your logo design should communicate.

```html
<!DOCTYPE html>
<html lang="en">
<head>
<meta charset="utf-8">
<title>Gravetto — Business Card</title>
<link rel="stylesheet" href="https://fonts.googleapis.com/css2?family=Marcellus&family=Open+Sans:wght@400&display=swap">
<style>
  :root {
    --page: #ecebe8;
    --ink-dark: #151515;
    --card-dark: #1b1b1b;
    --card-light: #ffffff;
    --text-light: #f4f4f4;
    --text-dark: #222222;
    --text-muted: #555555;
    --shadow: rgba(0, 0, 0, 0.18);
  }
  * { box-sizing: border-box; margin: 0; padding: 0; }
  html, body {
    width: 1200px;
    height: 900px;
    overflow: hidden;
    background: var(--page);
  }
  .canvas {
    width: 1200px;
    height: 900px;
    display: flex;
    flex-direction: column;
    align-items: center;
    justify-content: center;
    gap: 60px;
  }
  .card {
    position: relative;
    width: 620px;
    height: 354px;
    box-shadow: 0 10px 28px var(--shadow);
  }
  .card--front { background: var(--card-dark); color: var(--text-light); }
  .card--back  { background: var(--card-light); color: var(--text-dark); }

  .brand {
    display: flex;
    flex-direction: column;
    align-items: center;
  }
  .brand__mark {
    width: 44px;
    height: 44px;
    border: 2px solid currentColor;
    border-radius: 50%;
    margin-bottom: 22px;
  }
  .brand__name {
    font-family: "Marcellus", serif;
    font-size: 30px;
    letter-spacing: 0.42em;
    margin-right: -0.42em;
    text-transform: uppercase;
  }

  .card--front .brand {
    position: absolute;
    left: 0; right: 0;
    top: 92px;
  }
  .social-handle {
    position: absolute;
    left: 0; right: 0;
    top: 248px;
    text-align: center;
    font-family: "Open Sans", sans-serif;
    font-size: 15px;
    letter-spacing: 0.12em;
    color: var(--text-light);
  }

  .card--back .brand {
    position: absolute;
    left: 330px;
    width: 240px;
    top: 70px;
  }
  .card--back .brand__mark { border-color: var(--ink-dark); }

  .contact {
    position: absolute;
    left: 42px;
    bottom: 34px;
    font-family: "Open Sans", sans-serif;
  }
  .contact__name {
    font-family: "Marcellus", serif;
    font-size: 21px;
    letter-spacing: 0.02em;
    text-transform: uppercase;
    color: var(--text-dark);
  }
  .contact__role {
    font-size: 14px;
    color: var(--text-muted);
    margin-bottom: 18px;
  }
  .contact__list { list-style: none; }
  .contact__item {
    display: flex;
    align-items: center;
    gap: 10px;
    font-size: 13px;
    line-height: 22px;
    color: var(--text-dark);
  }
  .contact__icon {
    width: 12px;
    height: 12px;
    flex: none;
    fill: none;
    stroke: var(--ink-dark);
    stroke-width: 1.6;
  }
</style>
</head>
<body>
<main class="canvas">
  <section class="card card--front" aria-label="Card front">
    <div class="brand">
      <span class="brand__mark" aria-hidden="true"></span>
      <span class="brand__name">Gravetto</span>
    </div>
    <p class="social-handle">/gravetto</p>
  </section>

  <section class="card card--back" aria-label="Card back">
    <div class="brand">
      <span class="brand__mark" aria-hidden="true"></span>
      <span class="brand__name">Gravetto</span>
    </div>

    <div class="contact">
      <h1 class="contact__name">Samira Haddadin</h1>
      <p class="contact__role">Fashion Designer</p>
      <ul class="contact__list">
        <li class="contact__item">
          <svg class="contact__icon" viewBox="0 0 12 12" aria-hidden="true"><path d="M2.5 1.5 L4.5 1.5 L5 4 L3.8 4.8 Q5 7.2 7.2 8.2 L8 7 L10.5 7.5 L10.5 9.5 Q10.5 10.5 9.5 10.5 Q2 10 1.5 2.5 Q1.5 1.5 2.5 1.5 Z"/></svg>
          +971 4 555 0192
        </li>
        <li class="contact__item">
          <svg class="contact__icon" viewBox="0 0 12 12" aria-hidden="true"><rect x="3" y="1" width="6" height="10" rx="1"/><line x1="5.3" y1="9.2" x2="6.7" y2="9.2"/></svg>
          +971 50 555 0147
        </li>
        <li class="contact__item">
          <svg class="contact__icon" viewBox="0 0 12 12" aria-hidden="true"><rect x="1" y="2.5" width="10" height="7"/><polyline points="1,2.5 6,6.5 11,2.5"/></svg>
          info@gravetto-example.com
        </li>
        <li class="contact__item">
          <svg class="contact__icon" viewBox="0 0 12 12" aria-hidden="true"><circle cx="6" cy="6" r="5"/><ellipse cx="6" cy="6" rx="2.2" ry="5"/><line x1="1" y1="6" x2="11" y2="6"/></svg>
          www.gravetto-example.com
        </li>
      </ul>
    </div>
  </section>
</main>
</body>
</html>
```